Satchel & Sundial needs new business card design

I need a new business card design. I'm looking for out-of-the-box design which represents the freedom of being a location independent entrepreneur.
I offer coaching, retreats and trips.
I would like to see designs with and without the photo.
Colors I use are black (#000000), green (#25A796) and brown (#D7C38C)
Website satchelandsundial.example

Target Market(s)

location independent entrepreneurs, digital nomads, people looking to swap the 9 to 5 for a lifestyle business

Industry/Entity Type

Business

Contact Information for Business Card

Dorota Falkner
Your Lifestyle Business Coach, Retreat & Trip Leader
http://satchelandsundial.example
hello@satchelandsundial.example
Live a life you don't need a holiday from

Font styles to use
Serif
Sans Serif

Requirements
Must have
• One side should contain only the logo. I would also consider having the "Live a life you don't need a holiday from" on that side too (depending on how it looks)
• Please show both sides on the designs.

```html
<!DOCTYPE html>
<html lang="en">
<head>
<meta charset="utf-8">
<title>Satchel &amp; Sundial — Business Card</title>
<link rel="stylesheet" href="https://fonts.googleapis.com/css2?family=Open+Sans:ital,wght@0,400;0,600;0,700;1,400&display=swap">
<style>
  :root {
    --page-bg: #e6e6e6;
    --card-white: #ffffff;
    --brand-green: #25a796;
    --band-dark: #231f20;
    --ink: #1c1a1b;
    --pattern-tone: #f1f1f1;
    --pattern-tone-2: #e9eeed;
    --text-light: #ffffff;
  }
  html, body {
    margin: 0;
    padding: 0;
    width: 1105px;
    height: 1200px;
    overflow: hidden;
    background: var(--page-bg);
    font-family: "Open Sans", Arial, sans-serif;
  }
  .canvas {
    position: relative;
    width: 1105px;
    height: 1200px;
  }
  .card {
    position: absolute;
    left: 196px;
    width: 720px;
    height: 411px;
    background: var(--card-white);
    overflow: hidden;
  }
  .card--front { top: 146px; }
  .card--back { top: 602px; }

  .wordmark {
    position: absolute;
    left: 0;
    width: 100%;
    text-align: center;
    font-weight: 600;
    font-size: 52px;
    letter-spacing: 1px;
    color: var(--ink);
    line-height: 1;
  }
  .card--front .wordmark { top: 104px; }
  .card--back .wordmark { top: 184px; }

  .identity-band {
    position: absolute;
    left: 0;
    top: 259px;
    width: 100%;
    height: 74px;
    background: var(--brand-green);
    color: var(--text-light);
    text-align: center;
  }
  .identity-band__name {
    margin: 10px 0 0;
    font-weight: 600;
    font-size: 23px;
    letter-spacing: 0.5px;
    line-height: 1.2;
    text-transform: uppercase;
  }
  .identity-band__role {
    margin: 2px 0 0;
    font-size: 18px;
    line-height: 1.2;
  }
  .contact-band {
    position: absolute;
    left: 0;
    top: 337px;
    width: 100%;
    height: 74px;
    background: var(--band-dark);
    color: var(--text-light);
    font-size: 18px;
  }
  .contact {
    position: absolute;
    top: 25px;
    display: flex;
    align-items: center;
    gap: 10px;
    line-height: 1;
  }
  .contact--email { left: 32px; }
  .contact--web { right: 32px; }
  .contact svg { display: block; }

  .pattern-field {
    position: absolute;
    inset: 0;
    background: linear-gradient(160deg, var(--pattern-tone) 0%, #fafafa 45%, var(--pattern-tone-2) 100%);
  }
  .social-links {
    position: absolute;
    top: 26px;
    right: 24px;
    display: flex;
    gap: 5px;
  }
  .social-links span {
    display: block;
    width: 26px;
    height: 26px;
    background: var(--brand-green);
  }
  .motto {
    position: absolute;
    left: 0;
    top: 354px;
    width: 100%;
    text-align: center;
    font-style: italic;
    font-size: 18px;
    color: var(--ink);
  }
</style>
</head>
<body>
<main class="canvas">

  <section class="card card--front" aria-label="Card front">
    <div class="wordmark">Satchel &amp; Sundial</div>

    <div class="identity-band">
      <p class="identity-band__name">Dorota Falkner</p>
      <p class="identity-band__role">Your Lifestyle Business Coach, Retreat &amp; Trip Leader</p>
    </div>

    <div class="contact-band">
      <span class="contact contact--email">
        <svg width="18" height="13" viewBox="0 0 18 13" aria-hidden="true">
          <rect x="0" y="0" width="18" height="13" fill="var(--brand-green)"/>
          <path d="M0 0 L9 7 L18 0" fill="none" stroke="var(--band-dark)" stroke-width="1.5"/>
        </svg>
        hello@satchelandsundial.example
      </span>
      <span class="contact contact--web">
        satchelandsundial.example
        <svg width="18" height="18" viewBox="0 0 18 18" aria-hidden="true">
          <circle cx="9" cy="9" r="8" fill="var(--brand-green)"/>
          <ellipse cx="9" cy="9" rx="3.5" ry="8" fill="none" stroke="var(--band-dark)" stroke-width="1"/>
          <line x1="1" y1="9" x2="17" y2="9" stroke="var(--band-dark)" stroke-width="1"/>
        </svg>
      </span>
    </div>
  </section>

  <section class="card card--back" aria-label="Card back">
    <div class="pattern-field" role="img" aria-label="Faint repeated brand lettering pattern across the card background"></div>
    <div class="social-links" aria-label="Social profiles">
      <span></span><span></span><span></span>
    </div>
    <div class="wordmark">Satchel &amp; Sundial</div>
    <p class="motto">Live a life you don't need a holiday from</p>
  </section>

</main>
</body>
</html>
```